Business Card Design - Photographer

I am a landscape photographer and I require a business card design. 

I require two designs:
1)  a double sided business card
 and
b)  a single sided business card 

The single sided design can either be the same as the double sided (with just one side having all the information)....or it can be an entire new design. Its up to you.

My corporate colours are (CMYK):

Blue   69, 32, 0, 0
Grey  72,  64,  47,  31
Green  32,  2,  91,  0
Yellow   0, 19, 92, 0
Orange  0, 39, 75, 0

Colour space in final file should be in CMYK.

The details that need to be included on the card:

- Use the provided Logo
- Name: Wiktor Baranowski
- Email:   sales@vistalumeworks.com.au
- Website:    vistalumeworks.com.au
- Twitter:    twitter.com/vistalumeworks
- Facebook:   facebook.com/vistalumeworks
- Mobile  0417 539 662

Please use the attached template to design the logo to the specified size, including the marked bleed lines. I have also attached my logo in PNG (transparent background) and ai format for you to use.

The final file should be:
- Photoshop version with layers so I can edit the name/text etc. All non vector files should be high resolution at 1039 x 697 pixels at 300 dpi.

I also require a file as:
- Vector based PDF

Anyway questions please contact me.

Thank you

Industry/Entity Type

Landscape

Logo styles of interest
Pictorial/Combination Logo
Abstract Logo
Wordmark Logo
Lettermark Logo
Requirements
Must have
• The details that need to be included on the card:

- Use the provided Logo
- Name: Wiktor Baranowski
- Email: sales@vistalumeworks.com.au
- Website: vistalumeworks.com.au
- Twitter: twitter.com/vistalumeworks
- Facebook: facebook.com/vistalumeworks
- Mobile 0417 539 662

```html
<!DOCTYPE html>
<html lang="en">
<head>
<meta charset="utf-8">
<title>Vista Lume Works – Business Card</title>
<link rel="stylesheet" href="https://fonts.googleapis.com/css2?family=Source+Sans+3:wght@400&display=swap">
<style>
  :root {
    --card-bg: #ffffff;
    --page-bg: #ffffff;
    --ink: #0d0d0d;
    --frame: #1a1a1a;
    --brand-grey: #4a4d5c;
  }
  html, body {
    margin: 0;
    padding: 0;
    width: 1200px;
    height: 733px;
    overflow: hidden;
    background: var(--page-bg);
  }
  .card {
    position: relative;
    width: 1200px;
    height: 733px;
    box-sizing: border-box;
    border: 2px solid var(--frame);
    background: var(--card-bg);
    font-family: "Source Sans 3", "Myriad Pro", Arial, sans-serif;
    color: var(--ink);
    overflow: hidden;
  }
  .contact-list {
    position: absolute;
    left: 407px;
    top: 34px;
    margin: 0;
    padding: 0;
    list-style: none;
    font-size: 31px;
    line-height: 43px;
  }
  .contact-list li {
    position: relative;
    white-space: nowrap;
  }
  .contact-list .bulleted {
    padding-left: 110px;
  }
  .contact-list .bulleted::before {
    content: "-";
    position: absolute;
    left: 2px;
  }
  .brand-mark {
    position: absolute;
    left: 50px;
    top: 190px;
    width: 300px;
    height: 300px;
  }
  .brand-name {
    position: absolute;
    right: 14px;
    top: 486px;
    margin: 0;
    font-weight: 400;
    font-size: 116px;
    line-height: 1;
    letter-spacing: -1px;
    white-space: nowrap;
    color: var(--ink);
  }
  .owner-name {
    position: absolute;
    right: 18px;
    top: 625px;
    margin: 0;
    font-weight: 400;
    font-size: 31px;
    line-height: 43px;
    white-space: nowrap;
    color: var(--ink);
  }
</style>
</head>
<body>
  <div class="card">
    <ul class="contact-list">
      <li>Email: sales@vistalumeworks.com.au</li>
      <li class="bulleted">Website: vistalumeworks.com.au</li>
      <li class="bulleted">Twitter: twitter.com/vistalumeworks</li>
      <li class="bulleted">Facebook: facebook.com/vistalumeworks</li>
      <li class="bulleted">Mobile 0417 539 662</li>
    </ul>

    <svg class="brand-mark" viewBox="0 0 300 300" aria-hidden="true">
      <circle cx="150" cy="150" r="150" fill="var(--brand-grey)"/>
    </svg>

    <p class="brand-name">Vista Lume Works</p>
    <p class="owner-name">Wiktor Baranowski</p>
  </div>
</body>
</html>
```